Online Advice via Video Site requires Cutting Edge Homepage

We need a creative new and exciting webdesign for our tutoring via video-chat website.

We have prepared a "demo" homepage for you to see various promotional material that we think would be suitable for the homepage. http://www.quillmarsh.com/demo

The actual site is undergoing some final tinkering but can be accessed and used at http://www.quillmarsh.com

There is NO NEED to take any colours or design structure from this.

We expect the logo to be changed to match the new site. The new logo should match the site's function.

I have included some other projects that we like the look of:
http://www.vantoplex.com.au/design/143762
http://www.vantoplex.com.au/design/561630
http://www.vantoplex.com.au/design/247199
http://www.vantoplex.com.au/design/255195
http://www.birchlume.tv/

Target Market(s)

People that will work as tutors/advisers or be student/clients

Industry/Entity Type

Tutoring

Requirements
Must have
• The search is the main feature of the homepage

After the search the next goal of the page is to get people to sign up to the site

Login, (optional inclusion of the gablenet login - if you don't include it then you need only have a "login" button... no username or password input fields)

Footer
Nice to have
• The promotional material for the site, the colours on the Prezi file CAN BE changed to suit the new design you propose.

```html
<!DOCTYPE html>
<html lang="en">
<head>
<meta charset="utf-8">
<title>Quill Marsh – Online Advice via Video</title>
<link rel="stylesheet" href="https://fonts.googleapis.com/css2?family=Carlito:wght@400;700&family=Open+Sans:wght@400;600&display=swap">
<style>
:root{
  --page:#efeeef;
  --blue:#41628a;
  --blue-light:#5b86b8;
  --ink:#2b2b2b;
  --muted:#555;
  --white:#fff;
  --footer:#dddcdd;
  --panel-login:#a9c0d8;
  --black:#151515;
}
*{box-sizing:border-box;margin:0;padding:0}
html,body{width:765px;height:1200px;overflow:hidden}
body{position:relative;background:var(--page);font-family:"Open Sans",sans-serif;color:var(--ink)}
.abs{position:absolute}
.logo{left:38px;top:28px;font-family:"Carlito",sans-serif;font-weight:700;font-size:29px;color:var(--blue);white-space:nowrap}
.social-login{left:368px;top:14px;width:62px;height:18px;background:var(--blue);border:1px solid #2e4a6e;color:var(--white);font-size:7.5px;font-weight:600;line-height:16px;text-align:center;white-space:nowrap;overflow:hidden}
.login-panel{left:460px;top:5px;width:289px;height:35px;border-radius:5px;background:linear-gradient(#bcd0e4,var(--panel-login));}
.login-title{left:9px;top:8px;font-family:"Carlito",sans-serif;font-size:15px;color:var(--blue);display:flex;align-items:center;gap:3px}
.login-title i{display:inline-block;width:11px;height:11px;border-radius:50%;background:var(--blue)}
.field{height:14px;top:11px;background:var(--white);border:1px solid #8ba4bf;font-size:7px;font-style:italic;color:#999;padding-left:4px;line-height:12px}
.login-btn{left:249px;top:10px;width:30px;height:15px;background:var(--black);color:var(--white);font-size:8px;line-height:15px;text-align:center;border-radius:2px}
.remember{left:490px;top:48px;font-size:8px;color:#666;display:flex;align-items:center;gap:8px;white-space:nowrap}
.remember .box{width:9px;height:9px;border:1px solid var(--blue-light);background:var(--white)}
.join{left:672px;top:45px;width:59px;height:17px;border-radius:3px;background:linear-gradient(#7fa3cc,#4a74a6);color:var(--white);font-size:10px;line-height:17px;text-align:center}
.nav{left:20px;top:86px;width:724px;height:22px;background:#f7f7f7;font-size:11px;color:var(--blue)}
.nav span{position:absolute;top:0;line-height:22px;white-space:nowrap}
.nav .active{left:0;background:var(--blue-light);color:var(--white);width:59px;text-align:center}
.searchbar{left:15px;top:109px;width:735px;height:38px;background:linear-gradient(#fff,#e2e2e2);border:1px solid #d0d0d0}
.searchbar .label{left:26px;top:10px;font-size:14px;color:var(--blue);letter-spacing:.3px}
.searchbar .input{left:339px;top:7px;width:314px;height:22px;background:var(--white);border:1px solid #ccc;font-size:8px;font-style:italic;color:#999;padding-left:9px;line-height:20px}
.searchbar .go{left:663px;top:6px;width:54px;height:23px;background:var(--black);color:var(--white);font-size:11px;line-height:23px;text-align:center;border-radius:2px}
.hero{left:15px;top:155px;width:735px;height:302px;background:linear-gradient(90deg,#ddd9d3 0%,#c9c2b8 40%,#e8e6e1 70%,#b48c69 100%)}
.hero-quote{left:35px;top:213px;font-family:"Carlito",sans-serif;font-size:22.5px;line-height:30px;color:#1e1e1e;letter-spacing:.2px;white-space:nowrap}
.dots{left:388px;top:468px;display:flex;gap:4px}
.dots i{width:8px;height:8px;border-radius:50%;border:1px solid #bbb;background:#f6f6f6}
.dots i.on{background:var(--blue);border-color:var(--blue)}
.shadow{height:6px;background:radial-gradient(ellipse at center,rgba(0,0,0,.12),rgba(0,0,0,0) 70%)}
.tabs{left:22px;top:530px;display:flex;gap:2px;font-family:"Carlito",sans-serif;font-size:12.5px}
.tabs span{background:var(--blue);color:var(--white);height:19px;line-height:19px;text-align:center;white-space:nowrap}
.tabs span.on{background:var(--white);color:var(--blue);height:20px}
.tab-panel{left:15px;top:549px;width:408px;height:204px;background:var(--white);font-size:9.5px;color:#222}
.tab-panel li{list-style:none;height:20px;line-height:20px}
.tab-panel ul{padding:13px 0 0 28px}
.tab-panel li.sub{padding-left:27px;position:relative}
.tab-panel li.sub::before{content:"";position:absolute;left:16px;top:8px;width:5px;height:5px;border-radius:50%;background:var(--blue)}
.section-title{font-family:"Carlito",sans-serif;color:var(--blue);letter-spacing:.4px;white-space:nowrap}
.video{left:447px;top:567px;width:302px;height:187px;background:#cfcfcf;border:1px solid #bbb}
.video-screen{left:5px;top:3px;width:292px;height:152px;background:#111}
.video-scene{left:3px;top:3px;width:286px;height:126px;background:linear-gradient(90deg,#6b5136,#8a6a46 50%,#5c4630)}
.video-caption{left:15px;top:131px;font-family:"Carlito",sans-serif;font-size:14px;color:#5a82ad}
.video-bar{left:5px;top:157px;width:292px;height:28px}
.feature{left:16px;width:390px;height:70px}
.feature .thumb{left:0;top:0;width:106px;height:69px;border:3px solid var(--white);box-shadow:0 0 2px #bbb}
.feature h3{position:absolute;left:125px;top:1px;font-family:"Carlito",sans-serif;font-weight:400;font-size:13.5px;color:var(--blue);white-space:nowrap}
.feature p{position:absolute;left:125px;top:18px;width:262px;font-size:9px;line-height:12px;color:#444}
.feature .more{position:absolute;left:125px;top:59px;width:57px;height:12px;border-radius:2px;background:linear-gradient(#7fa3cc,#4a74a6);color:var(--white);font-size:7px;line-height:12px;text-align:center}
.topic{left:453px;width:296px}
.topic h4{font-family:"Carlito",sans-serif;font-weight:400;font-size:13px;color:#222}
.topic p{margin-top:4px;font-size:9px;line-height:13px;color:#444}
.footer{left:0;top:1133px;width:765px;height:67px;background:var(--footer)}
.footer-note{left:14px;top:31px;font-size:7.5px;color:#444;white-space:nowrap}
.footer-icons{left:659px;top:28px;display:flex;gap:13px}
.footer-icons i{width:12px;height:12px;display:block}
</style>
</head>
<body>

<div class="abs logo">Quill Marsh</div>
<div class="abs social-login">gablenet Log In</div>

<div class="abs login-panel">
  <div class="abs login-title"><i></i>Login</div>
  <div class="abs field" style="left:61px;width:88px">Username</div>
  <div class="abs field" style="left:156px;width:88px">Password</div>
  <div class="abs login-btn">Login</div>
</div>
<div class="abs remember"><span class="box"></span>Remember me <span>|</span> Forgot Password?</div>
<div class="abs join">Join Now</div>

<nav class="abs nav">
  <span class="active">Home</span>
  <span style="left:79px">Student</span>
  <span style="left:153px">Advisors</span>
  <span style="left:229px">Topics</span>
  <span style="left:296px">Blog</span>
  <span style="left:353px">FAQs</span>
  <span style="left:413px">Sitemap</span>
  <span style="left:489px">About us</span>
  <span style="left:567px">Our Technology</span>
  <span style="left:678px">Contact</span>
</nav>

<div class="abs searchbar">
  <div class="abs label">Search Topics and Advisors</div>
  <div class="abs input">Search</div>
  <div class="abs go">Search</div>
</div>

<div class="abs hero" role="img" aria-label="Photo of a woman writing on a clipboard beside a laptop in an office"></div>
<div class="abs hero-quote">"Imagine if, whenever you had a problem<br>you could instantly access the world's<br>experts to solve it. Now you can!"</div>
<div class="abs dots"><i class="on"></i><i></i><i></i></div>
<div class="abs shadow" style="left:20px;top:484px;width:725px"></div>

<div class="abs tabs">
  <span style="width:43px">Clients</span><span style="width:51px">Advisors</span><span style="width:54px">Students</span><span class="on" style="width:55px">Mentors</span><span style="width:52px">Mentees</span><span style="width:125px">Professional Advisors</span>
</div>
<div class="abs tab-panel">
  <ul>
    <li>Mentor where you have experience</li>
    <li>Support &amp; guide people</li>
    <li class="sub">Solve one off issues</li>
    <li class="sub">Provide ongoing mentoring</li>
    <li>Work when it suits you</li>
    <li class="sub">Pre-book appointments</li>
    <li class="sub">Answer questions only when you can</li>
    <li>Earn money for your time</li>
    <li class="sub">Set your own fee rate</li>
  </ul>
</div>

<div class="abs section-title" style="left:449px;top:531px;font-size:15px">QUILL MARSH</div>
<div class="abs video">
  <div class="abs video-screen">
    <div class="abs video-scene" role="img" aria-label="Video still of a presenter in front of bookshelves"></div>
    <svg class="abs" style="left:137px;top:55px" width="22" height="22" viewBox="0 0 22 22"><circle cx="11" cy="11" r="10" fill="rgba(255,255,255,.35)"/><path d="M8 6 L16 11 L8 16 Z" fill="#fff"/></svg>
    <div class="abs video-caption">Do you Know Somting</div>
  </div>
  <svg class="abs video-bar" width="292" height="28" viewBox="0 0 292 28">
    <rect x="0" y="2" width="232" height="5" fill="#9fb9d4"/>
    <text x="237" y="8" font-size="5" fill="#333" font-family="Open Sans, sans-serif">00:00:00 | 00:01:40</text>
    <rect x="0" y="13" width="8" height="8" fill="#eee" stroke="#888" stroke-width=".5"/>
    <rect x="12" y="16" width="20" height="2" fill="#888"/>
    <rect x="45" y="13" width="8" height="8" fill="#eee" stroke="#888" stroke-width=".5"/>
    <path d="M86 14v6l4-3zM96 14v6l-4-3zM112 14v6h1v-6zM116 14v6l-4-3zM138 13v8l6-4zM164 14v6l4-3zM172 14v6h1v-6zM180 14v6l4-3zM188 14v6l-4-3zM196 14h6v6h-6z" fill="#333"/>
    <rect x="278" y="12" width="10" height="10" fill="#eee" stroke="#888" stroke-width=".5"/>
  </svg>
</div>

<div class="abs feature" style="top:790px">
  <div class="abs thumb" role="img" aria-label="Photo of a student and tutor talking" style="background:linear-gradient(90deg,#b9b0c9,#7e92b5 50%,#c9b79e)"></div>
  <h3>Instant Personal Advice</h3>
  <p>Lorem Ipsum is simply dummy text of the printing and type-setting industry. Lorem Ipsum has been the industry's standard dummy text</p>
  <span class="more">read more</span>
</div>
<div class="abs feature" style="top:871px">
  <div class="abs thumb" role="img" aria-label="Photo of a video conference meeting" style="background:linear-gradient(90deg,#e3e3e3,#c8ccd2 50%,#efefef)"></div>
  <h3>Direct Video Conference</h3>
  <p>Lorem Ipsum is simply dummy text of the printing and type-setting industry. Lorem Ipsum has been the industry's standard dummy text</p>
  <span class="more">read more</span>
</div>
<div class="abs feature" style="top:955px">
  <div class="abs thumb" role="img" aria-label="Photo of advisors meeting with clients" style="background:linear-gradient(90deg,#7f95ac,#c9ccd0 50%,#5d6f86)"></div>
  <h3>Advisors and or Clients</h3>
  <p>Lorem Ipsum is simply dummy text of the printing and type-setting industry. Lorem Ipsum has been the industry's standard dummy text</p>
  <span class="more">read more</span>
</div>
<div class="abs feature" style="top:1037px">
  <div class="abs thumb" role="img" aria-label="Photo of a woman paying online with a card" style="background:linear-gradient(90deg,#f3efe9,#e6cdb0 50%,#f0ebe4)"></div>
  <h3>Payvane Or Credit Card</h3>
  <p>Lorem Ipsum is simply dummy text of the printing and type-setting industry. Lorem Ipsum has been the industry's standard dummy text</p>
  <span class="more">read more</span>
</div>

<div class="abs section-title" style="left:453px;top:789px;font-size:16px">ADVISORS BY TOPICS</div>
<div class="abs shadow" style="left:455px;top:810px;width:290px"></div>
<div class="abs topic" style="top:822px"><h4>Mathematics</h4><p>Lorem Ipsum is simply dummy text of the printing and typesetting industry. Lorem Ipsum has been the industry's standard dummy text ever since the 1500s, when an unknown printer</p></div>
<div class="abs shadow" style="left:455px;top:884px;width:290px"></div>
<div class="abs topic" style="top:895px"><h4>English</h4><p>Lorem Ipsum is simply dummy text of the printing and typesetting industry. Lorem Ipsum has been the industry's standard dummy text ever since the 1500s, when an unknown printer</p></div>
<div class="abs shadow" style="left:455px;top:957px;width:290px"></div>
<div class="abs topic" style="top:968px"><h4>Languages</h4><p>Lorem Ipsum is simply dummy text of the printing and typesetting industry. Lorem Ipsum has been the industry's standard dummy text ever since the 1500s, when an unknown printer</p></div>
<div class="abs shadow" style="left:455px;top:1030px;width:290px"></div>
<div class="abs topic" style="top:1041px"><h4>Technoligy</h4><p>Lorem Ipsum is simply dummy text of the printing and typesetting industry. Lorem Ipsum has been the industry's standard dummy text ever since the 1500s, when an unknown printer</p></div>
<div class="abs shadow" style="left:455px;top:1104px;width:290px"></div>

<footer class="abs footer">
  <div class="abs footer-note">© 2012 Quill Marsh - Terms of Service - Privacy Policy - Program Policies</div>
  <div class="abs footer-icons" aria-label="Social links">
    <i style="background:#3fa3d9"></i><i style="background:#3b5b99"></i><i style="background:#2a6fa8"></i><i style="background:#e8872c"></i>
  </div>
</footer>

</body>
</html>
```